A fantastic website for a physio

We are looking for an eye catching website which can attract as many customer as possible.
We have logo designed and ready to be used in the website.
Please use the green and blue which is used in our logo for the preferred colors.
The following are the designs that I Iike:
http://www.example-clinicone.com.au/
http://www.example-rehabtwo.com.au/
We will be having other services including massage therapy, Psychology and podiatrist. You can find information about podiatry in our condition sheet.
for the address you can put Shop 5/248 Wattlebrook Street, Kelvindale. It might change but for now you can leave it until I confirm that in the next couple of days.

Logo file can be downloaded here:
https://files.example-share.net/s/qz4mtl9wkr82bvx/Logo1511.jpg?dl=0

Target Market(s)

Infant to old people.
We speak Farsi.

Industry/Entity Type

Physical Therapy

Number of Pages Required

5+ page

Font styles to use
Serif

Colors
33a6d7
abd037
e667a6

Requirements
Must have
• Home, About , our services, Conditions we treat and contact
• For home page and contacts we would like a tab that can connect to another website(bookwell) for online booking. We would like the patient's to be able to leave us massage or leave their email for monthly news letter. For the condition we treat you can use the condition sheets I have attached. For about us and home page you can use brochure I have attached.
• The other things should have include: in-line contact form, Google Map, clinic hours, newsletter sign-up etc, schema rich contact information
• Social media connection to our Facebook, Instagram and linked in
Nice to have
• Search engine optimization for Merrylands and Parramatta physiotherapy.
• We can speak English and Farsi. So is nice to have an information tab for Farsi speaking people. I can provide you with the texts.

```html
<!DOCTYPE html>
<html lang="en">
<head>
<meta charset="utf-8">
<title>Aligned Physiotherapy – Therapy and Rehabilitation Clinic</title>
<link rel="stylesheet" href="https://fonts.googleapis.com/css2?family=Montserrat:wght@600;700;800&family=Open+Sans:wght@400;600;700&display=swap">
<style>
:root{
  --blue:#33a6d7;
  --blue-dark:#1f6fa3;
  --navy:#1b4f7c;
  --green:#abd037;
  --green-dark:#8db51e;
  --pink:#e667a6;
  --ink:#3a3f47;
  --muted:#7b828c;
  --line:#dfe5ea;
  --pale:#f3f7fa;
  --white:#fff;
}
*{box-sizing:border-box;margin:0;padding:0}
html,body{width:679px;height:1200px;overflow:hidden}
body{font-family:"Open Sans",Arial,sans-serif;color:var(--ink);background:var(--white);font-size:8px;line-height:1.5;position:relative}
h2,h3,.nav a,.btn{font-family:Montserrat,Arial,sans-serif}

/* top bar */
.topbar{height:30px;display:flex;align-items:center;justify-content:space-between;padding:0 32px;border-bottom:1px solid var(--line)}
.social{display:flex;gap:9px}
.social span{width:9px;height:9px;border-radius:2px;background:var(--muted)}
.contact-strip{display:flex;gap:12px;align-items:center;color:var(--muted);font-size:7px}
.contact-strip b{color:var(--blue);font-weight:600}
.lang{border:1px solid var(--line);padding:1px 6px;border-radius:2px}

/* header */
.header{height:48px;display:flex;align-items:center;justify-content:space-between;padding:0 32px}
.brand{display:flex;align-items:center;gap:7px}
.brand-dot{width:26px;height:26px;border-radius:50%;background:var(--blue)}
.brand-name{font-family:"Open Sans",sans-serif;font-weight:700;font-size:14px;color:var(--blue);line-height:1}
.nav{display:flex;gap:4px}
.nav a{font-size:7px;font-weight:700;color:var(--ink);text-decoration:none;padding:8px 11px;letter-spacing:.3px}
.nav a.active{color:var(--blue);border-bottom:2px solid var(--blue)}

/* hero */
.hero{position:relative;height:290px;background:linear-gradient(90deg,#eef2f3 0%,#e9eef0 38%,#dfe3e4 100%);overflow:hidden}
.hero-photo{position:absolute;right:0;top:0;width:440px;height:100%;background:linear-gradient(100deg,#e9eef0 0%,#d9c3b5 35%,#c9a996 55%,#b2c3cc 80%,#8fa7b4 100%)}
.hero-copy{position:absolute;left:40px;top:55px;width:260px}
.hero-copy .kicker{font-family:Montserrat,sans-serif;font-weight:800;font-size:17px;color:var(--green-dark);letter-spacing:.3px}
.hero-copy .tag{font-family:Montserrat,sans-serif;font-weight:700;font-size:15px;color:var(--blue);margin-top:2px}
.hero-copy .sub{font-family:Montserrat,sans-serif;font-weight:700;font-size:13px;color:var(--ink);margin-top:4px}
.btn{display:inline-block;background:var(--pink);color:#fff;font-size:7px;font-weight:700;padding:7px 14px;border-radius:12px;letter-spacing:.4px}
.hero-copy .btn{margin-top:20px}
.dots{position:absolute;left:40px;top:210px;display:flex;gap:5px}
.dots i{width:6px;height:6px;border-radius:50%;background:#9aa3ab}
.dots i:first-child{background:var(--ink)}
.hero-wave{position:absolute;left:0;bottom:0;width:679px;height:50px}

/* welcome */
.intro{display:flex;justify-content:space-between;padding:28px 32px 0 40px;height:200px}
.welcome{width:350px}
.sec-title{display:flex;align-items:center;gap:8px;margin-bottom:10px}
.sec-title h2{font-size:12px;font-weight:800;color:var(--green-dark);letter-spacing:.3px}
.sec-title h2.blue{color:var(--blue)}
.ico{width:20px;height:20px;border-radius:50%;background:var(--blue);display:flex;align-items:center;justify-content:center;flex:none}
.welcome p{color:var(--muted);font-size:7.5px}
.welcome .btn{margin-top:14px}
.hours{width:230px;height:168px;background:var(--green);border-radius:4px;padding:10px 14px;color:#fff}
.hours h3{font-size:11px;font-weight:800;display:flex;align-items:center;gap:6px;margin-bottom:6px}
.hours table{width:100%;border-collapse:collapse;font-size:7.5px}
.hours td{padding:3px 0;border-bottom:1px solid rgba(255,255,255,.35)}
.hours td:last-child{text-align:right}
.hours tr:last-child td{border:0;font-weight:700}

/* newsletter */
.newsletter{height:52px;background:var(--pink);display:flex;align-items:center;padding:0 40px;gap:16px;color:#fff}
.newsletter h2{font-size:12px;font-weight:800;letter-spacing:.4px}
.newsletter .field{width:150px;height:20px;background:#fff;border-radius:2px;color:var(--muted);font-size:7px;padding:5px 8px;margin-left:12px}
.newsletter .btn{background:var(--green);border-radius:2px;padding:6px 22px}
.ico.white{background:#fff}

/* services + booking */
.services-row{display:flex;justify-content:space-between;padding:22px 28px 0 40px;height:300px}
.services{width:375px}
.service{display:flex;gap:14px;padding:12px 0;border-bottom:1px solid var(--line)}
.service:last-child{border:0}
.svc-ico{width:38px;height:38px;border-radius:50%;flex:none;display:flex;align-items:center;justify-content:center}
.service h3{font-size:8.5px;font-weight:800;margin-bottom:3px}
.service p{color:var(--muted);font-size:7.5px}
.booking{width:218px;height:262px;border:1px solid var(--line);border-radius:4px;background:var(--pale);padding:10px 12px}
.booking .sec-title h2{color:var(--blue);font-size:10px}
.input{height:17px;background:#fff;border:1px solid var(--line);border-radius:9px;font-size:6.5px;color:var(--muted);padding:3px 9px;margin-bottom:6px}
.input.area{height:44px;border-radius:8px}
.book-foot{display:flex;justify-content:space-between;align-items:flex-end;margin-top:6px}
.powered{font-size:6px;color:var(--muted);line-height:1.2}
.powered b{display:block;font-size:9px;color:var(--navy);font-weight:700}
.booking .btn{border-radius:10px;padding:6px 16px}

/* footer */
.footer{position:absolute;left:0;top:920px;width:679px;height:280px;background:linear-gradient(180deg,#e7f3f8,#d6ecf5)}
.footer-wave{position:absolute;left:0;top:-14px;width:679px;height:30px}
.footer-cols{display:flex;gap:16px;padding:24px 32px 0 40px}
.loc{width:110px}
.footer h3{font-size:8.5px;font-weight:800;color:var(--navy);margin-bottom:8px}
.loc p{font-size:6.8px;color:var(--ink);display:flex;gap:5px;margin-bottom:4px;align-items:flex-start}
.map{width:140px;height:118px;border-radius:2px;background:linear-gradient(135deg,#e4e8dc,#d5dccb 60%,#c9d5e0)}
.quick{flex:1}
.quick-grid{display:grid;grid-template-columns:1fr 1fr;gap:6px}
.quick .input{border-radius:2px;margin:0}
.quick .area{height:40px;grid-row:span 2}
.quick .btn{float:right;margin-top:8px;border-radius:2px;padding:6px 22px}
.bottom{position:absolute;left:0;bottom:0;width:679px;height:48px;background:var(--navy);display:flex;align-items:center;justify-content:space-between;padding:0 32px;color:#cfe2ef;font-size:6.5px}
.bottom .brand-name{color:#fff;font-size:12px}
.bottom .brand-dot{width:20px;height:20px}
.bottom nav{display:flex;gap:6px}
</style>
</head>
<body>

<div class="topbar">
  <div class="social" aria-label="Social links"><span></span><span></span><span></span><span></span><span></span></div>
  <div class="contact-strip">
    <span><b>☏</b> +61 400 555 218</span>
    <span><b>✉</b> hello@alignedphysio.example</span>
    <span class="lang">English ▾</span>
  </div>
</div>

<header class="header">
  <div class="brand"><span class="brand-dot"></span><span class="brand-name">Aligned Physiotherapy</span></div>
  <nav class="nav">
    <a class="active" href="#">HOME</a><a href="#">ABOUT US</a><a href="#">SERVICES</a><a href="#">CONDITIONS WE TREAT</a><a href="#">CONTACT</a>
  </nav>
</header>

<section class="hero">
  <div class="hero-photo" role="img" aria-label="Physiotherapist treating a smiling patient's shoulder"></div>
  <div class="hero-copy">
    <div class="kicker">ALIGNED PHYSIOTHERAPY</div>
    <div class="tag">Let your Health Shine</div>
    <div class="sub">Therapy and Rehabilitation Clinic</div>
    <span class="btn">BOOK AN APPOINTMENT</span>
  </div>
  <div class="dots"><i></i><i></i><i></i><i></i></div>
  <svg class="hero-wave" viewBox="0 0 679 50" preserveAspectRatio="none">
    <path d="M0 30 C150 55 300 5 460 22 C560 32 630 20 679 8 L679 50 L0 50Z" fill="#fff"/>
    <path d="M0 30 C150 55 300 5 460 22 C560 32 630 20 679 8" fill="none" stroke="#33a6d7" stroke-width="3"/>
    <path d="M0 36 C160 58 320 12 470 28 C570 38 635 26 679 16" fill="none" stroke="#abd037" stroke-width="2"/>
  </svg>
</section>

<section class="intro">
  <div class="welcome">
    <div class="sec-title">
      <span class="ico"><svg width="10" height="10" viewBox="0 0 10 10"><path d="M4 0h2v4h4v2H6v4H4V6H0V4h4z" fill="#fff"/></svg></span>
      <h2>WELCOME TO OUR WEBSITE</h2>
    </div>
    <p>Our friendly team helps patients of every age move freely, recover from injury and stay active. We offer gentle hands-on care, clear advice and exercise plans built around your daily life and goals. Book your visit online today.</p>
    <span class="btn">READ MORE</span>
  </div>
  <div class="hours">
    <h3><svg width="12" height="12" viewBox="0 0 12 12"><circle cx="6" cy="6" r="5" fill="none" stroke="#fff" stroke-width="1.5"/><path d="M6 3v3l2 1.5" stroke="#fff" stroke-width="1.2" fill="none"/></svg>CLINIC HOURS</h3>
    <table>
      <tr><td>Monday</td><td>9:00 am to 7:00pm</td></tr>
      <tr><td>Tuesday</td><td>9:00 am to 7:00pm</td></tr>
      <tr><td>Wednesday</td><td>9:00 am to 7:00pm</td></tr>
      <tr><td>Thursday</td><td>9:00 am to 7:00pm</td></tr>
      <tr><td>Friday</td><td>9:00 am to 7:00pm</td></tr>
      <tr><td>Saturday</td><td>9:00 am to 7:00pm</td></tr>
      <tr><td>Sunday</td><td>Closed</td></tr>
    </table>
  </div>
</section>

<section class="newsletter">
  <span class="ico white"><svg width="10" height="10" viewBox="0 0 10 10"><path d="M4 0h2v4h4v2H6v4H4V6H0V4h4z" fill="#e667a6"/></svg></span>
  <h2>NEWSLETTER SIGN-UP</h2>
  <span class="field">Enter Email Address</span>
  <span class="btn">SIGN UP NOW</span>
</section>

<section class="services-row">
  <div class="services">
    <div class="sec-title">
      <span class="ico"><svg width="10" height="10" viewBox="0 0 10 10"><path d="M4 0h2v4h4v2H6v4H4V6H0V4h4z" fill="#fff"/></svg></span>
      <h2 class="blue">OUR SERVICES INCLUDE</h2>
    </div>
    <div class="service">
      <span class="svc-ico" style="background:var(--green)"><svg width="16" height="16" viewBox="0 0 16 16"><circle cx="8" cy="5" r="2.5" fill="#fff"/><rect x="2" y="9" width="12" height="3" rx="1.5" fill="#fff"/></svg></span>
      <div><h3 style="color:var(--green-dark)">MASSAGE THERAPY</h3><p>Relaxing treatment that eases tight muscles, improves circulation and supports faster recovery after sport or long working days.</p></div>
    </div>
    <div class="service">
      <span class="svc-ico" style="background:var(--blue)"><svg width="16" height="16" viewBox="0 0 16 16"><circle cx="8" cy="7" r="5" fill="none" stroke="#fff" stroke-width="1.6"/><path d="M6 14h4" stroke="#fff" stroke-width="1.6"/></svg></span>
      <div><h3 style="color:var(--blue)">PSYCHOLOGY</h3><p>Caring support for stress, anxiety and pain related worries, helping you build calm habits and a clearer mind.</p></div>
    </div>
    <div class="service">
      <span class="svc-ico" style="background:var(--pink)"><svg width="16" height="16" viewBox="0 0 16 16"><path d="M5 2h4v8h4v4H5z" fill="#fff"/></svg></span>
      <div><h3 style="color:var(--pink)">PODIATRIST</h3><p>Foot and ankle care for all ages, from heel pain and flat feet to custom orthotics and footwear advice.</p></div>
    </div>
  </div>

  <aside class="booking">
    <div class="sec-title">
      <span class="ico"><svg width="10" height="10" viewBox="0 0 10 10"><rect x="1" y="2" width="8" height="7" fill="none" stroke="#fff" stroke-width="1.2"/><path d="M1 4h8" stroke="#fff"/></svg></span>
      <h2>APPOINTMENT BOOKING</h2>
    </div>
    <div class="input">Name</div>
    <div class="input">Email Address</div>
    <div class="input">Phone no.</div>
    <div class="input">Subject ▾</div>
    <div class="input area">Message</div>
    <div class="book-foot">
      <div class="powered">Powered by<b>bookwell</b></div>
      <span class="btn">SUBMIT</span>
    </div>
  </aside>
</section>

<footer class="footer">
  <svg class="footer-wave" viewBox="0 0 679 30" preserveAspectRatio="none">
    <path d="M0 18 C180 0 360 30 520 14 C600 6 650 10 679 14 L679 30 L0 30Z" fill="#e7f3f8"/>
    <path d="M0 18 C180 0 360 30 520 14 C600 6 650 10 679 14" fill="none" stroke="#abd037" stroke-width="2"/>
  </svg>
  <div class="footer-cols">
    <div class="loc">
      <h3>LOCATION INFO</h3>
      <p><span>⌖</span>Shop 5/248 Wattlebrook Street, Kelvindale</p>
      <p><span>☏</span>+61 400 555 218</p>
      <p><span>✉</span>hello@alignedphysio.example</p>
      <p><span>◷</span>Map Direction</p>
    </div>
    <div class="map" role="img" aria-label="Street map showing the clinic location"></div>
    <div class="quick">
      <h3>QUICK CONTACT</h3>
      <div class="quick-grid">
        <div class="input">Full Name</div>
        <div class="input area">Message</div>
        <div class="input">Enter Email Address</div>
        <div class="input">Phone no.</div>
      </div>
      <span class="btn">SEND</span>
    </div>
  </div>
  <div class="bottom">
    <div class="brand"><span class="brand-dot"></span><span class="brand-name">Aligned Physiotherapy</span></div>
    <span>Copyright © Aligned Physiotherapy<br>All rights reserved</span>
    <nav><span>Home</span>|<span>About Us</span>|<span>Services</span>|<span>Conditions We Treat</span>|<span>Contact</span></nav>
  </div>
</footer>

</body>
</html>
```